TalkHarbor - Language Coaching Services

Sleek, innovative, trendy design for Language Coaching business.

TalkHarbor is a new UK based company that provides Language Coaching services. We offer highly personalized on-line and face to face language courses. We also impart learning techniques workshops based on the latest neuroscience research for second-language acquisition.

Target Market(s)

See attached info

Industry/Entity Type

Consulting

Contact Information for Business Card

TalkHarbor
DaniaKV@talkharbor.co.uk
TalkHarbor.co.uk
London, UK

Font styles to use
Sans Serif

```html
<!DOCTYPE html>
<html lang="en">
<head>
<meta charset="utf-8">
<title>TalkHarbor Business Cards</title>
<link rel="stylesheet" href="https://fonts.googleapis.com/css2?family=Roboto:wght@400;500;700&display=swap">
<style>
  :root{
    --bg:#a9abad;
    --blue-deep:#0a5f94;
    --blue-mid:#0d7fc0;
    --blue-bright:#17b1ea;
    --navy:#0b4a7a;
    --ink:#4a4f55;
    --white:#ffffff;
  }
  *{box-sizing:border-box;margin:0;padding:0}
  html,body{width:1200px;height:930px;overflow:hidden}
  body{background:var(--bg);font-family:"Roboto",sans-serif;position:relative}

  .card{position:absolute;width:560px;height:320px;border-radius:22px;overflow:hidden;
        box-shadow:0 10px 24px rgba(0,0,0,.25)}

  /* Services side */
  .card--services{left:60px;top:90px;color:var(--white);text-align:center;
        background:linear-gradient(120deg,var(--blue-bright) 0%,var(--blue-mid) 50%,var(--blue-deep) 100%)}
  .services__brand{display:flex;align-items:center;justify-content:center;gap:12px;margin-top:34px}
  .brand-dot{width:44px;height:44px;border:3px solid currentColor;border-radius:50%}
  .brand-name{font-family:"Roboto",sans-serif;font-weight:500;font-size:34px;letter-spacing:2px}
  .services__title{font-weight:700;font-size:20px;margin-top:16px}
  .services__rule{height:1px;background:rgba(255,255,255,.85);margin:8px 40px}
  .services__intro{font-size:15px;padding:2px 0}
  .services__list{font-size:14px;line-height:1.55;padding:2px 30px}

  /* Contact side */
  .card--contact{left:580px;top:520px;background:var(--white);border-bottom:10px solid var(--blue-bright)}
  .contact__mark{position:absolute;left:40px;top:40px;width:230px;height:230px;border-radius:50%;
        border:12px solid var(--blue-mid);display:flex;align-items:center;justify-content:center}
  .contact__mark .brand-name{color:var(--blue-mid);font-size:24px;letter-spacing:1px}
  .contact__divider{position:absolute;left:300px;top:40px;width:1px;height:230px;background:var(--blue-deep)}
  .contact__info{position:absolute;left:322px;top:40px;color:var(--ink)}
  .contact__info .brand-name{color:var(--blue-bright);font-size:26px;letter-spacing:1px;display:block}
  .person__name{font-weight:700;font-size:21px;color:var(--navy);margin-top:16px}
  .person__name span{color:var(--blue-bright)}
  .person__role{font-size:13px;margin-top:2px}
  .address{font-size:13px;line-height:1.5;margin-top:12px}
  .contact-list{list-style:none;font-size:13px;line-height:1.75;margin-top:10px}
  .contact-list li{display:flex;align-items:center;gap:7px}
  .contact-list svg{width:11px;height:11px;fill:var(--blue-deep)}
  .contact-list b{color:var(--navy)}
</style>
</head>
<body>

<section class="card card--services">
  <div class="services__brand">
    <span class="brand-dot"></span>
    <span class="brand-name">TALKHARBOR</span>
  </div>
  <h2 class="services__title">Our Services</h2>
  <div class="services__rule"></div>
  <p class="services__intro">We offer highly customized coaching sessions and self-study content.</p>
  <div class="services__rule"></div>
  <p class="services__list">
    Face to face language coaching sessions | On-line language coaching sessions<br>
    Personalized Newsletters for self-learners | Language Learning Techniques Workshops<br>
    Mindful Learning Workshops | Access to premium content, resources.
  </p>
</section>

<section class="card card--contact">
  <div class="contact__mark"><span class="brand-name">TALKHARBOR</span></div>
  <div class="contact__divider"></div>
  <div class="contact__info">
    <span class="brand-name">TALKHARBOR</span>
    <h1 class="person__name">ELENA <span>VARGA</span></h1>
    <p class="person__role">Director</p>
    <p class="address">52 Harbour Lane,<br>Bristol, UK, BS1 4QA</p>
    <ul class="contact-list">
      <li><svg viewBox="0 0 24 24"><path d="M6.6 10.8a15 15 0 0 0 6.6 6.6l2.2-2.2c.3-.3.7-.4 1-.2 1.1.4 2.3.6 3.6.6.6 0 1 .4 1 1V20c0 .6-.4 1-1 1A17 17 0 0 1 3 4c0-.6.4-1 1-1h3.5c.6 0 1 .4 1 1 0 1.3.2 2.5.6 3.6.1.3 0 .7-.2 1z"/></svg>(555) 014-2290</li>
      <li><svg viewBox="0 0 24 24"><path d="M2 5h20v14H2zm2 2v.5l8 5 8-5V7zm0 2.8V17h16V9.8l-8 5z"/></svg>info@talkharbor.co.uk</li>
      <li><svg viewBox="0 0 24 24"><circle cx="12" cy="12" r="10"/></svg>www.<b>talkharbor</b>.co.uk</li>
    </ul>
  </div>
</section>

</body>
</html>
```